Homemaking training schools needs a Business Card design

Designer, Hello!

No special requirements, good-looking enough.
--------------------------------------------------------------------------

Name: Marcus Dole
Chairman
Tel: 0574-71948263
Mobile: 13857420916
Email: kelvora@mailnest.example
Web: www.prt2019.example
Add: No.258, LanpingJie, BeiyuanQu, Ningbo, Zhejiang

LOGO
Ningbo PRT Homemaking Training School

Target Market(s)

pregnant women, mothers, infants, the elderly and families, including cleaning, cooking, nursing training.

Industry/Entity Type

Business

Contact Information for Business Card

Name: Marcus Dole
Chairman
Tel: 0574-71948263
Mobile: 13857420916
Email: kelvora@mailnest.example
Web: www.prt2019.example

LOGO

Font styles to use
Serif
Sans Serif
Decorative

Requirements
Nice to have
• Feels: clean, specifications, safety, comfort, warmth and happiness.

```html
<!DOCTYPE html>
<html lang="en">
<head>
<meta charset="utf-8">
<title>PingRuiTang Business Card</title>
<link href="https://fonts.googleapis.com/css2?family=Montserrat:wght@400;600;700&family=Quicksand:wght@400&display=swap" rel="stylesheet">
<style>
  :root {
    --bg: #2b2b2b;
    --card: #050505;
    --blue: #1a7fc8;
    --pink: #e2168a;
    --white: #f2f2f2;
  }
  html, body {
    margin: 0; padding: 0;
    width: 1200px; height: 900px;
    overflow: hidden;
    background: var(--bg);
    font-family: "Montserrat", sans-serif;
  }
  .stage { position: relative; width: 1200px; height: 900px; }
  .card {
    position: absolute;
    left: 290px;
    width: 620px; height: 354px;
    background: var(--card);
    box-shadow: 0 10px 30px rgba(0,0,0,.55);
    color: var(--white);
  }
  .card--front { top: 54px; }
  .card--back { top: 492px; }

  .brand { display: flex; flex-direction: column; align-items: flex-start; }
  .brand__row { display: flex; align-items: center; gap: 10px; }
  .brand__dot { width: 16px; height: 16px; border-radius: 50%; background: var(--pink); }
  .brand__name {
    font-family: "Montserrat", sans-serif;
    font-weight: 700; color: var(--blue);
    font-size: 42px; letter-spacing: -.5px; line-height: 1;
  }
  .brand__tagline {
    display: flex; align-items: center; gap: 10px;
    margin-top: 6px; width: 100%;
    font-family: "Quicksand", sans-serif;
    font-size: 17px; color: var(--white); white-space: nowrap;
  }
  .brand__tagline::before, .brand__tagline::after {
    content: ""; flex: 1; height: 1.5px; background: var(--white);
  }

  .card--front .brand { position: absolute; left: 50%; top: 120px; transform: translateX(-50%); width: 320px; }
  .front__url {
    position: absolute; left: 0; right: 0; top: 225px; text-align: center;
    color: var(--blue); font-weight: 700; font-size: 15px; letter-spacing: .3px;
  }

  .card--back .brand { position: absolute; left: 44px; top: 80px; width: 300px; }
  .back__rule { position: absolute; left: 0; right: 0; top: 222px; height: 1.5px; background: var(--blue); }
  .person { position: absolute; right: 36px; top: 180px; width: 190px; }
  .person__name { color: var(--blue); font-weight: 700; font-size: 21px; letter-spacing: .5px; line-height: 1; }
  .person__role { font-size: 11px; font-weight: 600; letter-spacing: .6px; margin-top: 5px; }
  .contacts { list-style: none; margin: 0; padding: 0; position: absolute; right: 20px; top: 242px; width: 206px; }
  .contacts li { display: flex; align-items: center; gap: 8px; font-size: 12px; font-weight: 600; line-height: 18px; }
  .contacts svg { width: 10px; height: 10px; flex: none; }
  .address { position: absolute; left: 44px; bottom: 36px; font-size: 12.5px; font-weight: 600; line-height: 18px; }
</style>
</head>
<body>
<div class="stage">
  <section class="card card--front">
    <div class="brand">
      <div class="brand__row"><span class="brand__dot"></span><span class="brand__name">PingRuiTang</span></div>
      <div class="brand__tagline">Training &amp; Services</div>
    </div>
    <div class="front__url">www.prt2019.example</div>
  </section>

  <section class="card card--back">
    <div class="brand">
      <div class="brand__row"><span class="brand__dot"></span><span class="brand__name">PingRuiTang</span></div>
      <div class="brand__tagline">Training &amp; Services</div>
    </div>
    <div class="person">
      <div class="person__name">MARCUS DOLE</div>
      <div class="person__role">CHAIRMAN</div>
    </div>
    <div class="back__rule"></div>
    <ul class="contacts">
      <li><svg viewBox="0 0 10 10"><path d="M2 1l2 2-1 1.2a6 6 0 0 0 2.8 2.8L7 6l2 2-1.2 1.2C4.5 9 1 5.5.8 2.2z" fill="#f2f2f2"/></svg>0574-71948263</li>
      <li><svg viewBox="0 0 10 10"><rect x="2.5" y=".5" width="5" height="9" rx="1" fill="none" stroke="#f2f2f2"/></svg>13857420916</li>
      <li><svg viewBox="0 0 10 10"><rect x=".5" y="2" width="9" height="6" fill="none" stroke="#f2f2f2"/><path d="M.5 2L5 5.5 9.5 2" fill="none" stroke="#f2f2f2"/></svg>kelvora@mailnest.example</li>
      <li><svg viewBox="0 0 10 10"><circle cx="5" cy="5" r="4.3" fill="none" stroke="#f2f2f2"/><path d="M.7 5h8.6M5 .7c-2.4 2.6-2.4 6 0 8.6M5 .7c2.4 2.6 2.4 6 0 8.6" fill="none" stroke="#f2f2f2" stroke-width=".8"/></svg>www.prt2019.example</li>
    </ul>
    <div class="address">258, LanpingJie<br>BeiyuanQu, Ningbo, Zhejiang</div>
  </section>
</div>
</body>
</html>
```